Book Cover for Fitness Trainer for Men

My name is Daisy Mae Corwin. I am a female Fitness Trainer for Men.
I need a new Book Cover Design for my second book and a back of the book.
Both with updated text.
#A… Book Cover… I like the bright red and yellow colors.
I like the weight rack and the bold headline Font
#B… Book Cover…I like the full frontal sexier body. I don not like the font style.
I want the new design sexier; super sexy. Even more eye catching for guys.
I want to push the envelope to the point of almost too much sexy.
An Brindle book 6”x9”, 150 pages

Target Market(s)

Men

Industry/Entity Type

Health and fitness for men

Colors
FFF300
FFF600
FEFA6F
FFFEC7
FFFEE8
EB3D1F
EC4F4E
F09395
F8D3D4
FCEDEE

Requirements
Must have
• Sexy & eye catching.

```html
<!DOCTYPE html>
<html lang="en">
<head>
<meta charset="utf-8">
<title>Daisy Mae Corwin – Fitness Trainer for Men – Book Cover Spread</title>
<link rel="stylesheet" href="https://fonts.googleapis.com/css2?family=Oswald:wght@700&family=Barlow+Condensed:ital,wght@0,500;0,600;0,700;1,600&family=Open+Sans:wght@600&family=Russo+One&display=swap">
<style>
  :root {
    --stage: #2b2b2b;
    --red: #e60a0a;
    --red-deep: #b80000;
    --yellow: #fff300;
    --yellow-warm: #ffe600;
    --white: #ffffff;
  }
  * { box-sizing: border-box; margin: 0; padding: 0; }
  html, body { width: 932px; height: 1200px; overflow: hidden; background: var(--stage); }

  .spread { position: absolute; left: 0; top: 250px; width: 932px; height: 700px; }
  .back-cover, .front-cover { position: absolute; top: 0; width: 466px; height: 700px; overflow: hidden; }
  .back-cover {
    left: 0;
    background: radial-gradient(ellipse at 55% 35%, #ff2518 0%, var(--red) 50%, var(--red-deep) 100%);
  }
  .front-cover { left: 466px; background: var(--red); }

  /* ---------- Back cover ---------- */
  .gym-backdrop {
    position: absolute; inset: 0;
    background: linear-gradient(135deg, rgba(110,0,0,.35) 0%, rgba(255,70,50,.12) 45%, rgba(110,0,0,.28) 100%);
  }
  .blurb {
    position: absolute; left: 0; top: 34px; width: 466px; text-align: center; color: var(--white);
    font-family: "Barlow Condensed", sans-serif; font-weight: 500;
    font-size: 10.8px; line-height: 13px; white-space: nowrap;
  }
  .blurb p + p { margin-top: 13px; }
  .testimonials {
    position: absolute; left: 0; top: 280px; width: 466px; text-align: center; color: var(--white);
    font-family: "Open Sans", sans-serif; font-weight: 600; font-size: 7.6px; line-height: 14px;
    white-space: nowrap;
  }
  .tagline, .mission {
    position: absolute; text-align: center; color: var(--yellow);
    font-family: "Russo One", sans-serif; font-style: italic; text-transform: uppercase; white-space: nowrap;
  }
  .tagline { left: 32px; width: 400px; top: 397px; font-size: 13.5px; line-height: 15px; letter-spacing: .6px; }
  .mission { left: 163px; width: 260px; top: 443px; font-size: 12.8px; line-height: 15px; letter-spacing: .5px; }
  .price-pitch {
    position: absolute; left: 175px; width: 270px; top: 558px; text-align: center; color: var(--white);
    font-family: "Barlow Condensed", sans-serif; font-weight: 700; font-size: 20px; line-height: 21px;
    text-transform: uppercase; white-space: nowrap;
  }
  .author-photo {
    position: absolute; left: 0; top: 436px; width: 228px; height: 264px;
    background:
      linear-gradient(90deg, rgba(230,10,10,0) 70%, rgba(200,10,10,.9) 100%),
      linear-gradient(180deg, rgba(200,10,10,.85) 0%, rgba(200,10,10,0) 18%),
      linear-gradient(160deg, #a86a3a 0%, #e2b48e 40%, #d59a70 65%, #2f6a66 100%);
  }
  .author-sign { position: absolute; left: 239px; top: 646px; width: 215px; }
  .author-sign .name {
    font-family: "Russo One", sans-serif; font-style: italic; color: var(--yellow-warm);
    font-size: 20px; line-height: 22px; text-transform: uppercase; white-space: nowrap;
  }
  .author-sign .role {
    font-family: "Barlow Condensed", sans-serif; font-weight: 700; color: var(--yellow-warm);
    font-size: 11.5px; line-height: 13px; text-transform: uppercase; white-space: nowrap;
  }

  /* ---------- Front cover ---------- */
  .front-cover { border-left: 1px solid rgba(150,0,0,.5); }
  .body-photo { position: absolute; inset: 0; }
  .weight-rack {
    position: absolute; left: 0; top: 563px; width: 158px; height: 137px;
    background:
      linear-gradient(90deg, rgba(230,10,10,0) 80%, rgba(120,80,50,.4) 100%),
      linear-gradient(180deg, #3c3c3c 0%, #161616 35%, #7a7a7a 46%, #1c1c1c 56%, #0c0c0c 100%);
  }
  .title-line {
    position: absolute; left: 17px; line-height: 1; white-space: nowrap;
    font-family: "Oswald", sans-serif; font-weight: 700; text-transform: uppercase;
  }
  .author-title { color: var(--white); font-size: 39px; letter-spacing: 3px; }
  .book-title { color: var(--yellow-warm); }
  .subtitle {
    position: absolute; left: 16px; top: 460px; white-space: nowrap;
    font-family: "Barlow Condensed", sans-serif; font-style: italic; font-weight: 600; color: var(--white);
    font-size: 17px; line-height: 17.3px; text-transform: uppercase; letter-spacing: .3px;
  }
  .badge { position: absolute; left: 119px; top: 436px; width: 144px; height: 144px; }
</style>
</head>
<body>
<main class="spread">

  <section class="back-cover">
    <div class="gym-backdrop" role="img" aria-label="Blurred red-tinted gym interior background"></div>

    <div class="blurb">
      <p>I’ve been using eye candy to get guys interested in health and fitness since the day I walked in the gym and<br>turned heads. I figured if you wanted Tits &amp; Ass I’d give it to you. Enough to make a buck and get my guys<br>healthier. As a personal fitness trainer for Men I’ve learned…that not all Guys are the same. Each of you is<br>different and You need to find what works for You. When you do … the the pounds melt away, your gut shrinks,<br>and your health improves.</p>
      <p>You’ll love the new you. Your girl friend will love it. Your wife will love it.<br>Nothing a woman loves more than a long rock hard man in shape.</p>
      <p>While everybody in the fitness community screams and yells about gym memberships, 30 day challenges,<br>and complete diet changes … My Guys don’t do all that. My Guys are Real Men with Real bodies. Real Men that<br>work for a living and don’t have time to live in the gym.</p>
      <p>Real men are tired of gym rats with “Look at me” egos, God given 1% body fat and abs you’ll never get.<br>These guys are full of Shit! And they’re the first one to buy my book. Ya gotta love it.<br>You need to find what works for you.<br>“I made a few adjustment in my meals added a minimum amount of exercise and lost 17 pounds in three<br>months. Thanks Daisy. Couldn’t have done it without you.”</p>
    </div>

    <p class="testimonials">“Daisy I took your bait and it actually made sense. Can’t believe you got me exercising. My gut shrunk<br>and had to buy new pants. Best 20 bucks I ever spent.” “I’ve tried a few expensive 30day programs but<br>your Ultimate Workout was all I ever needed. You’re right No F**king secret here.” “Strategically eating<br>Fast food is genius. Never thought I could still eat “the good stuff” and lose weight. WOW!” “My<br>increasing weight was scaring the hell out of me. Showing me that it’s the little changes I can do…that<br>has changed everything.” “Everybody wanted me to make big drastic changes in my life. I can’t do that.<br>All these little “Tricks of the Trade” I can do.” Thank you Daisy.”</p>

    <p class="tagline">Real men can be fit, healthy and in shape no<br>matter their size, weight, or body fat.</p>

    <div class="author-photo" role="img" aria-label="Portrait photo of the author smiling, in a teal lace top"></div>

    <p class="mission">My mission is to get your<br>lazy ass in shape by finding<br>what works for you.<br>If I need to get your<br>attention first…then<br>that’s what I’ll do.</p>

    <p class="price-pitch">Think you can do twenty bucks<br>to get you hot, sweaty,<br>and hard?</p>

    <div class="author-sign">
      <div class="name">Daisy Mae Corwin</div>
      <div class="role">Fitness Trainer for Men</div>
    </div>
  </section>

  <section class="front-cover">
    <svg class="body-photo" viewBox="0 0 466 700" role="img" aria-label="Photo of a tanned toned female torso in a yellow bikini">
      <defs>
        <linearGradient id="torsoTones" x1="0" y1="0" x2="0" y2="1">
          <stop offset="0" stop-color="#a8653a"/>
          <stop offset=".12" stop-color="#d9a36b"/>
          <stop offset=".24" stop-color="#f2cf1e"/>
          <stop offset=".36" stop-color="#d8a066"/>
          <stop offset=".55" stop-color="#b97b4a"/>
          <stop offset=".7" stop-color="#d6a064"/>
          <stop offset=".82" stop-color="#f3d01c"/>
          <stop offset="1" stop-color="#e9c21a"/>
        </linearGradient>
        <linearGradient id="torsoShade" x1="0" y1="0" x2="1" y2="0">
          <stop offset="0" stop-color="#6e3a1c" stop-opacity=".45"/>
          <stop offset=".5" stop-color="#ffffff" stop-opacity="0"/>
          <stop offset="1" stop-color="#6e3a1c" stop-opacity=".25"/>
        </linearGradient>
      </defs>
      <path d="M100,0 C150,55 225,140 238,230 C248,300 250,380 232,430 C210,480 160,520 146,560 C140,600 150,650 158,700 L466,700 L466,0 Z" fill="url(#torsoTones)"/>
      <path d="M100,0 C150,55 225,140 238,230 C248,300 250,380 232,430 C210,480 160,520 146,560 C140,600 150,650 158,700 L466,700 L466,0 Z" fill="url(#torsoShade)"/>
    </svg>

    <div class="weight-rack" role="img" aria-label="Photo of a dumbbell weight rack"></div>

    <div class="title-line author-title" style="top:64.5px">Daisy</div>
    <div class="title-line author-title" style="top:108.5px">Mae</div>
    <div class="title-line author-title" style="top:152.5px">Corwin</div>

    <h1 class="book-title">
      <span class="title-line" style="top:196px;font-size:54px">Fitness</span>
      <span class="title-line" style="top:252px;font-size:56px">Trainer</span>
      <span class="title-line" style="top:303px;font-size:104px">For</span>
      <span class="title-line" style="top:405px;font-size:47px;letter-spacing:1px">Men</span>
    </h1>

    <p class="subtitle">So pounds<br>melt away,<br>your gut<br>shrinks, &amp;<br>you last<br>longer.</p>

    <svg class="badge" viewBox="-72 -72 144 144" aria-label="Helping guys get hot, sweaty, and hard">
      <polygon fill="#ffe600" points="72,0 58,15.5 62.4,36 42.4,42.4 36,62.4 15.5,58 0,72 -15.5,58 -36,62.4 -42.4,42.4 -62.4,36 -58,15.5 -72,0 -58,-15.5 -62.4,-36 -42.4,-42.4 -36,-62.4 -15.5,-58 0,-72 15.5,-58 36,-62.4 42.4,-42.4 62.4,-36 58,-15.5"/>
      <g transform="rotate(-14)" fill="#e60a0a" font-family="Russo One, sans-serif" text-anchor="middle">
        <text x="0" y="-22" font-size="17">HELPING</text>
        <text x="0" y="-5" font-size="17">GUYS</text>
        <text x="0" y="9" font-size="12">GET HOT,</text>
        <text x="0" y="22" font-size="12">SWEATY, &amp;</text>
        <text x="0" y="35" font-size="12">HARD</text>
      </g>
    </svg>
  </section>

</main>
</body>
</html>
```